Business Card for a Dental Office

The design should communicate integrity, quality and reliability. We also want the card look elegant, simple, but still stand out, different from the traditional-dental-office business card.

Industry/Entity Type

Business

```html
<!DOCTYPE html>
<html lang="en">
<head>
<meta charset="utf-8">
<title>Harlow Dental Studio – Business Card</title>
<link rel="stylesheet" href="https://fonts.googleapis.com/css2?family=Open+Sans:wght@400;600;700&display=swap">
<style>
  :root {
    --backdrop: #3b3431;
    --card: #0d0d0d;
    --card-edge: #1a1a1a;
    --gold: #e0b81a;
    --white: #f4f4f4;
    --muted: #d9d9d9;
    --rule: #3a3a3a;
  }
  * { margin: 0; padding: 0; box-sizing: border-box; }
  html, body { width: 1200px; height: 844px; overflow: hidden; }
  body {
    background: var(--backdrop);
    font-family: "Open Sans", Arial, sans-serif;
    display: flex;
    align-items: center;
    justify-content: center;
    gap: 50px;
  }
  .card {
    width: 540px;
    height: 310px;
    background: var(--card);
    border: 1px solid var(--card-edge);
    border-radius: 4px;
    position: relative;
    box-shadow: 0 18px 40px rgba(0,0,0,0.45);
  }
  .brand {
    display: flex;
    align-items: center;
    gap: 12px;
  }
  .brand-mark {
    width: 34px;
    height: 34px;
    background: var(--gold);
    flex: none;
  }
  .brand-text { line-height: 1; }
  .brand-name {
    font-weight: 700;
    font-size: 24px;
    color: var(--white);
    text-transform: uppercase;
    letter-spacing: 0.5px;
  }
  .brand-tagline {
    margin-top: 5px;
    font-weight: 700;
    font-size: 11.5px;
    color: var(--gold);
    text-transform: uppercase;
    letter-spacing: 0.6px;
  }

  /* Front: contact side */
  .card-front .brand { position: absolute; left: 40px; top: 58px; }
  .person {
    position: absolute;
    left: 40px;
    top: 172px;
    width: 225px;
    text-align: right;
    line-height: 1.25;
  }
  .person-name { font-size: 21px; color: var(--gold); font-weight: 400; }
  .person-role { font-size: 14px; color: var(--white); }
  .person-address { margin-top: 14px; font-size: 14px; color: var(--white); }
  .divider {
    position: absolute;
    left: 285px;
    top: 160px;
    width: 1px;
    height: 112px;
    background: var(--rule);
  }
  .contact-list {
    position: absolute;
    left: 305px;
    top: 160px;
    list-style: none;
  }
  .contact-item {
    display: flex;
    align-items: center;
    gap: 12px;
    font-size: 14px;
    color: var(--muted);
    height: 22px;
  }
  .contact-icon { width: 12px; height: 12px; flex: none; fill: var(--gold); }

  /* Back: logo side */
  .card-back { display: flex; align-items: center; justify-content: center; }
</style>
</head>
<body>

  <section class="card card-front">
    <div class="brand">
      <span class="brand-mark"></span>
      <div class="brand-text">
        <div class="brand-name">Harlow Dental Studio</div>
        <div class="brand-tagline">Your smile is your gift to others</div>
      </div>
    </div>

    <div class="person">
      <div class="person-name">Daniel Mercer</div>
      <div class="person-role">Managing Director</div>
      <div class="person-address">12345, Address Goes Here<br>Country Name, 123456</div>
    </div>

    <div class="divider"></div>

    <ul class="contact-list">
      <li class="contact-item">
        <svg class="contact-icon" viewBox="0 0 24 24" aria-hidden="true"><path d="M6.6 10.8a15.1 15.1 0 0 0 6.6 6.6l2.2-2.2a1 1 0 0 1 1-.25 11.4 11.4 0 0 0 3.6.57 1 1 0 0 1 1 1V20a1 1 0 0 1-1 1A17 17 0 0 1 3 4a1 1 0 0 1 1-1h3.5a1 1 0 0 1 1 1c0 1.25.2 2.45.57 3.57a1 1 0 0 1-.25 1z"/></svg>
        (044)-456-7890
      </li>
      <li class="contact-item">
        <svg class="contact-icon" viewBox="0 0 24 24" aria-hidden="true"><path d="M6 2h12v6H6zM3 9h18a1 1 0 0 1 1 1v7h-4v5H6v-5H2v-7a1 1 0 0 1 1-1zm5 7v4h8v-4z"/></svg>
        123-456-7890
      </li>
      <li class="contact-item">
        <svg class="contact-icon" viewBox="0 0 24 24" aria-hidden="true"><path d="M2 5h20v14H2zm2 2v.5l8 5 8-5V7z"/></svg>
        info@youremail.com
      </li>
      <li class="contact-item">
        <svg class="contact-icon" viewBox="0 0 24 24" aria-hidden="true"><path d="M12 2a10 10 0 1 0 0 20 10 10 0 0 0 0-20zm6.9 6h-3a15 15 0 0 0-1.4-3.9A8 8 0 0 1 18.9 8zM12 4c.8 1.2 1.5 2.5 1.9 4h-3.8c.4-1.5 1.1-2.8 1.9-4zM4.3 14a8 8 0 0 1 0-4h3.4a16 16 0 0 0 0 4zm.8 2h3a15 15 0 0 0 1.4 3.9A8 8 0 0 1 5.1 16zm3-8h-3a8 8 0 0 1 4.4-3.9A15 15 0 0 0 8.1 8zM12 20c-.8-1.2-1.5-2.5-1.9-4h3.8c-.4 1.5-1.1 2.8-1.9 4zm2.3-6H9.7a14 14 0 0 1 0-4h4.6a14 14 0 0 1 0 4zm.2 5.9a15 15 0 0 0 1.4-3.9h3a8 8 0 0 1-4.4 3.9zM16.3 14a16 16 0 0 0 0-4h3.4a8 8 0 0 1 0 4z"/></svg>
        www.website.com
      </li>
    </ul>
  </section>

  <section class="card card-back">
    <div class="brand">
      <span class="brand-mark"></span>
      <div class="brand-text">
        <div class="brand-name">Harlow Dental Studio</div>
        <div class="brand-tagline">Your smile is your gift to others</div>
      </div>
    </div>
  </section>

</body>
</html>
```